Automotive eCommerce Business looking for a business card design

Looking for a clean and simple business card design. Our company name is "Brindle Auto" and we are a company specializing in the ecommerce sales of automotive parts, specifically for pick up trucks and large SUVs. Our company colours are red, black, and white.

Feel free to use the logo provided or create a new logo that you seem fit. Looking forward to your creative ideas!

Industry/Entity Type

Automotive

Contact Information for Business Card

We were thinking of a possibly two-sided design featuring just the logo and company name on one side, and personal information on the other side. Single sided designs will be considered as well.

Font styles to use
Serif
Sans Serif
Decorative

Colors
ec1f27
ffffff
000000

Requirements
Must have
• Space for employee's name, title, phone number and email address, along with the company address and website somewhere.

```html
<!DOCTYPE html>
<html lang="en">
<head>
<meta charset="utf-8">
<title>Brindle Auto – Business Card</title>
<link rel="stylesheet" href="https://fonts.googleapis.com/css2?family=Roboto:wght@400&family=Roboto+Condensed:wght@400;500&display=swap">
<style>
  :root {
    --stage: #6e4c34;
    --slate: #4b4f51;
    --brand-red: #a51d24;
    --white: #ffffff;
    --card-shadow: rgba(0, 0, 0, 0.35);
  }
  * { margin: 0; padding: 0; box-sizing: border-box; }
  html, body { width: 1200px; height: 960px; overflow: hidden; }
  body {
    position: relative;
    background: var(--stage);
    font-family: "Roboto", Arial, sans-serif;
  }
  .card {
    position: absolute;
    width: 600px;
    height: 342px;
    border-radius: 18px;
    overflow: hidden;
    box-shadow: 0 4px 10px var(--card-shadow);
  }

  /* Back side */
  .card-back {
    left: 322px;
    top: 108px;
    background: var(--slate);
    color: var(--white);
  }
  .card-back .brand-name {
    position: absolute;
    left: 0; right: 0;
    top: 152px;
    text-align: center;
    font-family: "Roboto Condensed", Arial, sans-serif;
    font-weight: 500;
    font-size: 38px;
    line-height: 44px;
  }
  .card-back .website {
    position: absolute;
    left: 0; right: 0;
    top: 296px;
    text-align: center;
    font-size: 15px;
    letter-spacing: 5px;
  }

  /* Front side */
  .card-front {
    left: 320px;
    top: 492px;
    background: var(--brand-red);
    color: var(--white);
  }
  .card-front .brand-panel {
    position: absolute;
    left: 0; top: 0;
    width: 600px; height: 342px;
  }
  .card-front .brand-name {
    position: absolute;
    left: 293px;
    width: 307px;
    top: 92px;
    text-align: center;
    font-family: "Roboto Condensed", Arial, sans-serif;
    font-weight: 500;
    font-size: 30px;
    line-height: 36px;
    color: var(--brand-red);
  }
  .person {
    position: absolute;
    left: 34px;
    top: 28px;
    font-family: "Roboto Condensed", Arial, sans-serif;
    text-transform: uppercase;
  }
  .person .name { font-size: 22px; line-height: 28px; font-weight: 500; }
  .person .role { font-size: 15px; line-height: 18px; font-weight: 400; }
  .address {
    position: absolute;
    left: 34px;
    top: 172px;
    font-style: normal;
    font-size: 14.5px;
    line-height: 18px;
  }
  .contacts {
    position: absolute;
    left: 34px;
    top: 218px;
    list-style: none;
    font-size: 14.5px;
    line-height: 19.2px;
  }
  .contacts li { display: flex; align-items: center; }
  .contacts svg { width: 14px; height: 14px; margin-right: 9px; fill: var(--white); }
</style>
</head>
<body>

<section class="card card-back">
  <p class="brand-name">Brindle Auto</p>
  <p class="website">www.brindleparts.com</p>
</section>

<section class="card card-front">
  <svg class="brand-panel" viewBox="0 0 600 342" aria-hidden="true">
    <path d="M293 0 H600 V178 L482 234 Q455 247 428 234 L306 176 Q293 170 293 156 Z" fill="#ffffff"/>
  </svg>
  <p class="brand-name">Brindle Auto</p>

  <div class="person">
    <p class="name">Marcus Reed</p>
    <p class="role">CEO/Founder</p>
  </div>

  <address class="address">
    4120 Harlow Street<br>
    Bramford, Ohio 44820
  </address>

  <ul class="contacts">
    <li><svg viewBox="0 0 16 16"><path d="M3.6 1.5l2.3 2.4-1.2 1.8c.9 2 2.4 3.5 4.5 4.5l1.8-1.2 2.4 2.3-1.4 2.2C7.2 13.2 2.8 8.8 1.5 3z"/></svg>555 214 7730</li>
    <li><svg viewBox="0 0 16 16"><path d="M4.5 1h7v14h-7zM5.8 2.5v9.5h4.4V2.5zM7.3 13h1.4v1H7.3z" fill-rule="evenodd"/></svg>555 386 1942</li>
    <li><svg viewBox="0 0 16 16"><path d="M4 2h8v4H4zM1 7h14v6h-2v-2H3v2H1zM4 12h8v3H4z"/></svg>555 903 5518</li>
    <li><svg viewBox="0 0 16 16"><path d="M1 4h14v9H1z"/><path d="M2.3 5.3L8 9.3l5.7-4" fill="none" stroke="#a51d24" stroke-width="1.2"/></svg>hello@brindleparts.com</li>
    <li><svg viewBox="0 0 16 16"><circle cx="8" cy="8" r="6.5"/><path d="M4 6l2 1 1 3-1 2M10 3l-1 3 2 1 2-1" fill="none" stroke="#a51d24" stroke-width="1.3"/></svg>www.brindleparts.com</li>
  </ul>
</section>

</body>
</html>
```